Brookvale Building Company - advertisement poster

I am looking to print some canvas signs to advertise my general contracting company, Brookvale Building Company. The sign will measure 6' long x 3' high so the size should match that ratio. I already have a logo icon, which is the Letter 'B' and some trees that I would like to incorporate, see attached. I would also like the to have the following information listed:
1) phone number: 831-555-0172
2) email: brookvalebuildingcompany@mailnest.example
3) website: brookvalebuildingcompany.example
4) Lic#4826130
5) I want to use this text: "BUILD WITH THE B-CREW!"

The ad should be relatively simple and clean. Black and Green are my company colors. I am open to creative ideas!

Target Market(s)

People looking to renovate their homes

Industry/Entity Type

Construction

Colors
59FF00
82FF00
B8FF75
E3FFCB
F4FFEA

Requirements
Must have
• Must have my company logo
Should not have
• No photos or complex graphics

```html
<!DOCTYPE html>
<html lang="en">
<head>
<meta charset="utf-8">
<title>Brookvale Building Company – Build With The B-Crew</title>
<link rel="stylesheet" href="https://fonts.googleapis.com/css2?family=Michroma&family=Poppins:wght@500;600;700&display=swap">
<style>
  :root {
    --navy: #161e64;
    --green: #6db544;
    --white: #ffffff;
    --ink: #1b1b1b;
  }
  * { margin: 0; padding: 0; box-sizing: border-box; }
  html, body { width: 1200px; height: 674px; overflow: hidden; background: var(--white); }
  .sign {
    position: relative;
    width: 1200px;
    height: 674px;
    background: var(--white);
    font-family: "Poppins", sans-serif;
    overflow: hidden;
  }
  .sign__top {
    position: absolute; left: 0; top: 0;
    width: 1200px; height: 340px;
    background: var(--navy);
  }
  .sign__edge { position: absolute; left: 0; top: 300px; width: 1200px; height: 80px; }
  .headline {
    position: absolute; left: 42px; top: 52px;
    font-family: "Michroma", sans-serif;
    line-height: 1;
    text-transform: uppercase;
  }
  .headline__line { display: block; white-space: nowrap; }
  .headline__line--green { color: var(--green); font-size: 88px; letter-spacing: 1px; }
  .headline__line--white { color: var(--white); font-size: 88px; margin-top: 34px; letter-spacing: 1px; }

  .brand {
    position: absolute; left: 42px; top: 420px;
    width: 320px;
    display: flex; align-items: center; gap: 14px;
  }
  .brand__mark { width: 34px; height: 34px; flex: none; background: var(--green); }
  .brand__name {
    font-family: "Poppins", sans-serif;
    font-weight: 700;
    font-size: 32px;
    line-height: 1.1;
    color: var(--navy);
    text-transform: uppercase;
  }

  .phone {
    position: absolute; left: 408px; top: 378px;
    display: flex; align-items: center; gap: 30px;
  }
  .phone__icon { width: 68px; height: 68px; flex: none; }
  .phone__number {
    font-weight: 700; font-size: 92px; line-height: 1;
    color: var(--ink); letter-spacing: -3px;
  }

  .licence {
    position: absolute; left: 411px; top: 503px;
    width: 152px; height: 83px;
    border: 3px solid var(--navy); border-radius: 8px;
    overflow: hidden; text-align: center;
  }
  .licence__label {
    background: var(--navy); color: var(--white);
    font-weight: 500; font-size: 24px; line-height: 36px;
  }
  .licence__number {
    color: var(--ink); font-weight: 500; font-size: 25px; line-height: 42px; letter-spacing: 1px;
  }

  .contact {
    position: absolute; left: 592px; top: 500px;
    list-style: none;
  }
  .contact__item {
    display: flex; align-items: center; gap: 16px;
    font-weight: 500; font-size: 21px; color: var(--ink);
    height: 30px; margin-bottom: 19px; white-space: nowrap;
  }
  .contact__icon { width: 26px; height: 26px; flex: none; }
</style>
</head>
<body>
<main class="sign">
  <div class="sign__top"></div>
  <svg class="sign__edge" viewBox="0 0 1200 80" preserveAspectRatio="none" aria-hidden="true">
    <polygon fill="#6db544" points="0,40 0,26 40,30 90,34 140,28 190,24 240,30 300,32 360,26 420,30 470,36 520,40 580,38 640,34 700,30 760,24 800,18 860,22 920,28 980,30 1030,34 1060,38 1100,36 1140,28 1200,20 1200,40 1160,46 1120,52 1080,60 1040,64 1000,56 950,50 900,48 850,44 800,40 760,44 700,50 640,54 580,56 520,58 470,54 420,48 360,46 300,50 240,48 190,42 140,46 90,48 40,44"/>
    <polygon fill="#161e64" points="0,0 1200,0 1200,20 1140,28 1100,36 1060,38 1030,34 980,30 920,28 860,22 800,18 760,24 700,30 640,34 580,38 520,40 470,36 420,30 360,26 300,32 240,30 190,24 140,28 90,34 40,30 0,26"/>
  </svg>

  <h1 class="headline">
    <span class="headline__line headline__line--green">Build With</span>
    <span class="headline__line headline__line--white">The B-Crew!</span>
  </h1>

  <div class="brand">
    <span class="brand__mark" aria-hidden="true"></span>
    <span class="brand__name">Brookvale Building Company</span>
  </div>

  <div class="phone">
    <svg class="phone__icon" viewBox="0 0 68 68" aria-hidden="true">
      <circle cx="34" cy="34" r="34" fill="#161e64"/>
      <path d="M22 18c2-1 4 0 5 2l3 6c1 2 0 3-1 4l-2 2c1 4 5 8 9 10l2-2c1-1 3-2 4-1l6 3c2 1 3 3 2 5l-2 4c-1 2-3 3-5 3-13-2-23-12-25-25 0-2 1-4 4-5z" fill="#ffffff"/>
      <path d="M38 20a12 12 0 0 1 10 10M38 13a19 19 0 0 1 17 17" fill="none" stroke="#ffffff" stroke-width="3" stroke-linecap="round"/>
    </svg>
    <span class="phone__number">831-555-0172</span>
  </div>

  <div class="licence">
    <div class="licence__label">Licence</div>
    <div class="licence__number">#4826130</div>
  </div>

  <ul class="contact">
    <li class="contact__item">
      <svg class="contact__icon" viewBox="0 0 26 26" aria-hidden="true">
        <circle cx="13" cy="13" r="13" fill="#6db544"/>
        <rect x="6" y="8" width="14" height="10" fill="#161e64"/>
        <path d="M6 8l7 6 7-6" fill="none" stroke="#ffffff" stroke-width="1.4"/>
      </svg>
      brookvalebuildingcompany@mailnest.example
    </li>
    <li class="contact__item">
      <svg class="contact__icon" viewBox="0 0 26 26" aria-hidden="true">
        <circle cx="13" cy="13" r="13" fill="#6db544"/>
        <circle cx="13" cy="13" r="7" fill="none" stroke="#161e64" stroke-width="1.6"/>
        <path d="M6 13h14M13 6c-4 4-4 10 0 14M13 6c4 4 4 10 0 14" fill="none" stroke="#161e64" stroke-width="1.4"/>
      </svg>
      www.brookvalebuildingcompany.example
    </li>
  </ul>
</main>
</body>
</html>
```